Wordpress Site Design for a Horror and Action Movie Production Company

We need a re-design/facelift of our website: https://k42t.pagecraft.io
The structure of the website could remain the same, but it needs to look and feel BETTER!

We would like the website coded in Wordpress so that it can be easily updated bu us, via adding new projects and new projects' info.

We specialize in Action, Horror, and Sci-Fi Genre. That being said, we don't want the website to look like it's a themed park with haunted houses. It should still be sharp and professional, as after all - it is a business for us!

Target Market(s)

Film Distribution Companies (B2B), as well as general audience that likes movies

Industry/Entity Type

Movie Production

Coding

Coded - Design and coding required

Number of Pages Required

5+ page

Font styles to use
Sans Serif

Colors

Designer to choose colors to be used in the design.

Requirements
Must have
• - PROJECTS page
• - Each PROJECT has a sub-page with project info/updates (up dates could be in a form of a WP post, ideally a template that we can use to update and create new PROJECT pages, with text, poster, and video link (trailer))
• - NEWS page that chronologically lists updates from all PROJECTS (could be done via WP blog)
• - HOME page would
Nice to have
• Should generally have a dark background.
• Websites we like as a reference of general approach and style:
• https://marbletoq.com
• https://velunpix.com (however this is very image-centric, and we might not have that much imagery at the moment)
• https://www.copperfieldechoandframe.com/other
• https://quennreels.com
Should not have
• We specialize in Action, Horror, and Sci-Fi Genre. That being said, we don't want the website to look like it's a themed park with haunted houses. It should still be sharp and professional, as after all - it is a business for us!

```html
<!DOCTYPE html>
<html lang="en">
<head>
<meta charset="utf-8">
<title>Kestrel 42 Media</title>
<link href="https://fonts.googleapis.com/css2?family=Roboto:wght@400;500;700&family=Open+Sans:wght@400;600&display=swap" rel="stylesheet">
<style>
:root{
  --bg-dark:#1e1c1d;
  --bg-deep:#0f0a0b;
  --red:#c10000;
  --red-bright:#e00a0a;
  --white:#ffffff;
  --text-light:#e4e4e4;
  --text-muted:#8d8b8c;
  --card-text:#a3a3a3;
  --footer:#151314;
  --icon:#d6d6d6;
}
*{box-sizing:border-box;margin:0;padding:0}
html,body{width:1200px;height:4454px;overflow:hidden}
body{position:relative;background:var(--bg-dark);font-family:"Open Sans",Arial,sans-serif;color:var(--text-light)}
.abs{position:absolute}
h1,h2,h3,.nav a,.btn,.brand{font-family:"Roboto",Arial,sans-serif}
.section-title{position:absolute;left:0;width:1200px;text-align:center;font-size:30px;font-weight:700;color:var(--white);letter-spacing:.3px}

/* header */
.site-header{left:0;top:0;width:1200px;height:140px;background:var(--bg-dark)}
.brand{left:110px;top:48px;color:var(--white);font-size:26px;font-weight:700;letter-spacing:1px}
.call{left:640px;top:28px;display:flex;align-items:center;gap:8px;font-family:"Roboto",sans-serif;font-size:13px;color:var(--white)}
.call strong{font-size:19px;font-weight:500}
.search{left:922px;top:20px;width:166px;height:40px;border-radius:20px;background:var(--white);padding:0 16px;display:flex;align-items:center;justify-content:space-between;font-size:13px;color:#777}
.nav{left:638px;top:96px}
.nav a{position:absolute;white-space:nowrap;font-size:13px;font-weight:700;color:var(--white);text-decoration:none}
.nav a.active{color:var(--red-bright)}

/* hero */
.hero-media{left:0;top:140px;width:1200px;height:620px;background:
  radial-gradient(ellipse 110px 260px at 760px 380px,rgba(20,14,12,.85),rgba(20,14,12,0) 100%),
  radial-gradient(ellipse 260px 200px at 280px 210px,rgba(190,150,120,.45),rgba(190,150,120,0) 100%),
  radial-gradient(ellipse 520px 380px at 560px 330px,#6a2e26 0%,rgba(90,36,30,.6) 50%,rgba(40,18,16,0) 100%),
  linear-gradient(100deg,#0e0a0a 0%,#2a1414 22%,#4a221d 45%,#3a1b17 65%,#1a0f0e 85%,#0c0909 100%)}
.hero h1{left:112px;top:382px;font-size:40px;font-weight:700;color:var(--white)}
.hero p{left:113px;top:440px;width:540px;font-size:15px;line-height:26px;color:var(--text-light)}
.dots{display:flex;gap:10px}
.dots span{width:38px;height:4px;background:var(--red)}

/* about */
.about h2{left:112px;top:912px;font-size:30px;font-weight:700;color:var(--white)}
.about p{left:112px;top:968px;width:505px;font-size:14.5px;line-height:26px;text-align:justify;color:var(--text-light)}
.btn{display:flex;align-items:center;justify-content:center;gap:6px;background:var(--red);color:var(--white);font-size:14px;font-weight:700;text-decoration:none}
.about-media{left:675px;top:857px;width:400px;height:390px;border-radius:50%;border:4px solid var(--red);background:
  radial-gradient(ellipse 120px 90px at 210px 110px,rgba(120,70,60,.7),rgba(120,70,60,0)),
  radial-gradient(ellipse 90px 120px at 320px 150px,rgba(60,80,110,.55),rgba(60,80,110,0)),
  radial-gradient(ellipse 150px 80px at 260px 330px,rgba(150,20,20,.7),rgba(150,20,20,0)),
  linear-gradient(160deg,#d8c4b8 0%,#a48a80 35%,#5e4a48 65%,#1e1616 100%)}
.play{width:52px;height:52px;border-radius:50%;background:var(--white);display:flex;align-items:center;justify-content:center}

/* projects */
.projects-bg{left:0;top:1340px;width:1200px;height:630px;background:var(--bg-deep)}
.card{width:247px;height:284px;background:var(--white);top:1528px}
.card-media{position:absolute;left:0;top:0;width:247px;height:160px;border:3px solid var(--red)}
.card h3{position:absolute;top:176px;width:100%;text-align:center;font-size:14px;font-weight:700;color:#111}
.card p{position:absolute;top:202px;left:8px;right:8px;text-align:center;font-size:13.5px;line-height:22px;color:var(--card-text)}

/* partners */
.partners-bg{left:0;top:1966px;width:1200px;height:650px;background:linear-gradient(180deg,#1d1a1b,#262223)}
.partner-badge{width:272px;height:272px;border-radius:50%;background:var(--white);border:5px solid var(--red);box-shadow:0 0 0 4px #1d1a1b inset;display:flex;align-items:center;justify-content:center}
.partner-name{width:440px;text-align:center;font-family:"Roboto",sans-serif;font-size:17px;font-weight:500;color:var(--white);top:2417px}
.partner-desc{width:440px;text-align:center;font-size:14px;line-height:22px;color:var(--text-muted);top:2446px}

/* team */
.team-bg{left:0;top:2616px;width:1200px;height:700px;background:
  radial-gradient(ellipse 500px 300px at 600px 350px,rgba(45,40,42,.6),rgba(45,40,42,0)),
  linear-gradient(180deg,#1b1819,#161314)}
.portrait{border:4px solid var(--white)}
.member-name{left:645px;top:2820px;font-family:"Roboto",sans-serif;font-size:20px;font-weight:500;color:var(--white)}
.member-role{left:645px;top:2853px;font-size:16px;color:var(--text-light)}
.member-bio{left:645px;top:2890px;width:440px;font-size:14px;line-height:25px;color:var(--text-light)}
.arrow{width:28px;height:28px;border-radius:50%;border:2px solid var(--red);display:flex;align-items:center;justify-content:center}
.social{top:2825px;width:18px;height:18px;display:flex;align-items:center;justify-content:center}

/* completed */
.completed-bg{left:0;top:3312px;width:1200px;height:560px;background:linear-gradient(180deg,#151213,#1c1819)}
.completed h2{left:112px;top:3405px;font-size:30px;font-weight:700;color:var(--white)}
.completed p{left:112px;top:3462px;width:448px;font-size:14.5px;line-height:26px;text-align:justify;color:var(--text-light)}
.video{left:614px;top:3412px;width:466px;height:303px;background:
  radial-gradient(ellipse 60px 50px at 380px 90px,rgba(230,120,80,.55),rgba(230,120,80,0)),
  radial-gradient(ellipse 50px 70px at 430px 200px,rgba(200,60,40,.5),rgba(200,60,40,0)),
  radial-gradient(ellipse 140px 170px at 150px 150px,rgba(120,90,70,.75),rgba(120,90,70,0)),
  linear-gradient(100deg,#1e1a18 0%,#3d2e26 35%,#4a2a1e 65%,#2a1610 100%)}

/* contact */
.contact-bg{left:0;top:3835px;width:1200px;height:540px;background:linear-gradient(90deg,#2a2424 0%,#1e1a1a 45%,#171414 100%)}
.contact-scene{left:0;top:3855px;width:600px;height:520px;background:
  radial-gradient(ellipse 200px 120px at 160px 120px,rgba(110,100,95,.45),rgba(110,100,95,0)),
  radial-gradient(ellipse 160px 140px at 400px 330px,rgba(70,60,58,.6),rgba(70,60,58,0)),
  linear-gradient(160deg,#3b3331 0%,#262121 55%,#1a1616 100%)}
.contact h2{left:626px;top:3940px;font-size:30px;font-weight:700;color:var(--white)}
.field{border:2px solid #cfcfcf;font-size:14px;color:var(--white);padding:12px 10px}
.submit{left:630px;top:4272px;width:455px;height:43px}

footer{left:0;top:4375px;width:1200px;height:79px;background:var(--footer);display:flex;align-items:center;justify-content:center;font-size:14px;color:var(--text-light)}
</style>
</head>
<body>

<header class="abs site-header">
  <div class="abs brand">KESTREL 42 MEDIA</div>
  <div class="abs call">
    <svg width="26" height="26" viewBox="0 0 26 26"><circle cx="13" cy="13" r="11.5" fill="none" stroke="#fff" stroke-width="1.6"/><path d="M9 7.5l2.2 2.4-1.3 1.6c.8 1.8 2.2 3.3 4 4.1l1.6-1.3 2.4 2.2-1.4 2c-4.2-.5-8-4.3-8.5-8.6z" fill="#fff"/></svg>
    <span>CALL US : <strong>555-010-4242</strong></span>
  </div>
  <div class="abs search"><span>Search</span>
    <svg width="14" height="14" viewBox="0 0 14 14"><circle cx="6" cy="6" r="4.5" fill="none" stroke="#333" stroke-width="1.6"/><path d="M9.3 9.3L13 13" stroke="#333" stroke-width="1.8"/></svg>
  </div>
  <nav class="abs nav">
    <a class="active" style="left:0">HOME</a>
    <a style="left:86px">ABOUT</a>
    <a style="left:178px">NEWS</a>
    <a style="left:262px">PROJECTS</a>
    <a style="left:382px">CONTACT</a>
  </nav>
</header>

<section class="hero">
  <div class="abs hero-media" role="img" aria-label="Action heroine holding a pistol against a dark red wooden wall under a lamp"></div>
  <h1 class="abs">KESTREL 42 MEDIA</h1>
  <p class="abs">is a fresh brand of multi-media entertainment, aimed at development of original Canadian content</p>
  <div class="abs dots" style="left:535px;top:681px"><span></span><span></span><span></span></div>
  <svg class="abs" style="left:0;top:700px" width="1200" height="70" viewBox="0 0 1200 70">
    <path d="M0 20 Q600 70 1200 20 L1200 70 L0 70Z" fill="var(--bg-dark)"/>
    <path d="M0 20 Q600 70 1200 20" fill="none" stroke="var(--red)" stroke-width="4"/>
  </svg>
</section>

<section class="about">
  <h2 class="abs">ABOUT US</h2>
  <p class="abs">Kestrel 42 Media Inc (K42M) is a fresh brand of multi-media Visual Content, aimed at development of original Canadian content as well as servicing of foreign productions here at home, in Ontario, Canada.K42M is a child of a partnership between two Canadian companies, which for years have been recognized as key brands in the Canadian media landscape:</p>
  <a class="abs btn" style="left:112px;top:1152px;width:136px;height:44px">READ MORE
    <svg width="16" height="10" viewBox="0 0 16 10"><path d="M0 5h14M10 1l4 4-4 4" fill="none" stroke="#fff" stroke-width="1.6"/></svg></a>
  <div class="abs about-media" role="img" aria-label="Film poster still of a tattooed man covering his face"></div>
  <div class="abs play" style="left:831px;top:1022px"><svg width="18" height="20" viewBox="0 0 18 20"><path d="M3 1l14 9-14 9z" fill="#222"/></svg></div>
</section>

<section class="projects">
  <div class="abs projects-bg"></div>
  <svg class="abs" style="left:0;top:1330px" width="1200" height="60" viewBox="0 0 1200 60">
    <path d="M0 60 L0 50 Q600 -10 1200 50 L1200 60Z" fill="var(--bg-deep)"/>
    <path d="M0 50 Q600 -10 1200 50" fill="none" stroke="var(--red)" stroke-width="4"/>
  </svg>
  <h2 class="section-title" style="top:1440px">OUR PROJECTS</h2>

  <article class="abs card" style="left:85px">
    <div class="card-media" role="img" aria-label="Boxer training with a punching bag" style="background:radial-gradient(ellipse 50px 70px at 170px 70px,rgba(200,150,120,.7),rgba(200,150,120,0)),linear-gradient(90deg,#1e1818 0%,#5c4a42 30%,#d8d2cc 45%,#6a5448 60%,#2a2020 100%)"></div>
    <h3>NORTHFALL</h3><p>Feature Film Executive Produced by Polar Flag, a Ashcrow Pictures brand</p>
  </article>
  <article class="abs card" style="left:341px">
    <div class="card-media" role="img" aria-label="Sci-fi title art over a planet surface" style="background:radial-gradient(ellipse 90px 40px at 120px 110px,rgba(200,200,205,.7),rgba(200,200,205,0)),linear-gradient(180deg,#15171c 0%,#2e323a 35%,#7a7e86 60%,#2a2c32 100%)"></div>
    <h3>DARK CURRENT</h3><p>Feature Film serviced by K42M, directed by Currently in post-production</p>
  </article>
  <article class="abs card" style="left:594px">
    <div class="card-media" role="img" aria-label="Trailer still of a woman in shadow" style="background:radial-gradient(ellipse 60px 70px at 100px 75px,rgba(110,80,82,.7),rgba(110,80,82,0)),linear-gradient(120deg,#0f0b0c,#2e2224,#0d0a0b)"></div>
    <div class="abs play" style="left:104px;top:60px;width:38px;height:38px"><svg width="13" height="15" viewBox="0 0 18 20"><path d="M3 1l14 9-14 9z" fill="#222"/></svg></div>
    <h3>NEON RIDER</h3><p>Feature Film Executive Produced by Ashcrow Pictures</p>
  </article>
  <article class="abs card" style="left:851px">
    <div class="card-media" role="img" aria-label="Figure standing in a derelict industrial room" style="background:radial-gradient(ellipse 40px 70px at 70px 85px,rgba(150,120,90,.7),rgba(150,120,90,0)),linear-gradient(100deg,#2e3430 0%,#59605a 40%,#8a8a80 70%,#3a3e38 100%)"></div>
    <h3>GONE TOO DEEP</h3><p>Feature Film Produced by Ninefold Lumen Entertainment, Pure Grain brand</p>
  </article>

  <div class="abs dots" style="left:546px;top:1858px"><span style="width:32px"></span><span style="width:32px;background:#5a0a0a"></span><span style="width:32px"></span></div>
</section>

<section class="partners">
  <div class="abs partners-bg"></div>
  <svg class="abs" style="left:0;top:1920px" width="1200" height="60" viewBox="0 0 1200 60">
    <path d="M0 0 L1200 0 L1200 10 Q600 70 0 10Z" fill="var(--bg-deep)"/>
    <path d="M0 10 Q600 70 1200 10" fill="none" stroke="var(--red)" stroke-width="4"/>
  </svg>
  <h2 class="section-title" style="top:2063px">OUR PARTNERS</h2>
  <div class="abs partner-badge" style="left:234px;top:2116px"><div style="width:170px;height:110px;background:#1a1a1a;border-radius:8px"></div></div>
  <div class="abs partner-badge" style="left:679px;top:2116px"><div style="width:210px;height:80px;background:#1a1a1a"></div></div>
  <div class="abs partner-name" style="left:150px">Ashcrow Pictures Inc</div>
  <div class="abs partner-desc" style="left:150px">Ashcrow Pictures is led by partners<br>It represents unique, innovative and cutting edge<br>genre films for North American distribution</div>
  <div class="abs partner-name" style="left:595px">Ninefold Lumen Entertainment Inc</div>
  <div class="abs partner-desc" style="left:595px">Ninefold Lumen is founded Tomas Reyn csc in<br>gained momentum. It has been behind the<br>production of a feature film Gone</div>
</section>

<section class="team">
  <div class="abs team-bg"></div>
  <h2 class="section-title" style="top:2710px">OUR TEAM</h2>
  <div class="abs portrait" role="img" aria-label="Portrait of a smiling man in a suit holding a phone" style="left:342px;top:2812px;width:286px;height:398px;background:radial-gradient(ellipse 70px 90px at 140px 120px,rgba(200,160,130,.85),rgba(200,160,130,0)),radial-gradient(ellipse 18px 80px at 140px 300px,rgba(180,20,30,.9),rgba(180,20,30,0)),linear-gradient(180deg,#ecebe9 0%,#d6d4d2 30%,#3a4f86 55%,#22336a 100%)"></div>
  <div class="abs portrait" role="img" aria-label="Black and white team portrait" style="left:152px;top:3062px;width:170px;height:150px;background:radial-gradient(ellipse 40px 50px at 80px 60px,#9a9a9a,rgba(154,154,154,0)),linear-gradient(135deg,#5a5a5a,#1e1e1e)"></div>
  <div class="abs portrait" role="img" aria-label="Black and white team portrait" style="left:657px;top:3062px;width:172px;height:150px;background:radial-gradient(ellipse 40px 50px at 86px 62px,#a8a8a8,rgba(168,168,168,0)),linear-gradient(135deg,#6a6a6a,#262626)"></div>
  <div class="abs portrait" role="img" aria-label="Black and white team portrait" style="left:860px;top:3062px;width:172px;height:150px;background:radial-gradient(ellipse 40px 50px at 90px 60px,#b0b0b0,rgba(176,176,176,0)),linear-gradient(135deg,#7a7a7a,#2e2e2e)"></div>
  <div class="abs member-name">MARCUS VALE</div>
  <div class="abs member-role">Writer/Producer/Director</div>
  <p class="abs member-bio">Marcus T Vale is an award-winning Writer/Producer/Director with over 15 years experience in the film and television industry. Marcus's feature length directorial debut “Bitter Bloom” premiered at the 2009 Nightreel Film Festival in Montreal,</p>
  <div class="abs social" style="left:1010px" aria-label="Share"><svg width="12" height="12" viewBox="0 0 12 12"><circle cx="9.5" cy="2.5" r="1.8" fill="var(--icon)"/><circle cx="2.5" cy="6" r="1.8" fill="var(--icon)"/><circle cx="9.5" cy="9.5" r="1.8" fill="var(--icon)"/><path d="M2.5 6L9.5 2.5M2.5 6l7 3.5" stroke="var(--icon)" stroke-width="1"/></svg></div>
  <div class="abs social" style="left:1040px" aria-label="Email"><svg width="13" height="10" viewBox="0 0 13 10"><rect x=".6" y=".6" width="11.8" height="8.8" fill="none" stroke="var(--icon)" stroke-width="1.2"/><path d="M.6 .6l5.9 5 5.9-5" fill="none" stroke="var(--icon)" stroke-width="1.2"/></svg></div>
  <div class="abs social" style="left:1070px" aria-label="Link"><svg width="13" height="13" viewBox="0 0 13 13"><path d="M5.5 7.5l2-2M4.5 6L3 7.5a2 2 0 0 0 2.8 2.8L7.3 8.8M8.5 7L10 5.5a2 2 0 0 0-2.8-2.8L5.7 4.2" fill="none" stroke="var(--icon)" stroke-width="1.3" stroke-linecap="round"/></svg></div>
  <div class="abs arrow" style="left:1019px;top:3016px"><svg width="10" height="12" viewBox="0 0 10 12"><path d="M7 1L2 6l5 5" fill="none" stroke="#fff" stroke-width="1.6"/></svg></div>
  <div class="abs arrow" style="left:1057px;top:3016px"><svg width="10" height="12" viewBox="0 0 10 12"><path d="M3 1l5 5-5 5" fill="none" stroke="#fff" stroke-width="1.6"/></svg></div>
</section>

<section class="completed">
  <div class="abs completed-bg"></div>
  <h2 class="abs">COMPLETED PROJECTS</h2>
  <p class="abs">Sed ut perspiciatis unde omnis iste natus error sit voluptatem accusantium doloremque laudantium, totam rem aperiam, eaque ipsa quae ab illo inventore veritatis et quasi architecto beatae vitae dicta sunt explicabo. Nemo enim ipsam voluptatem quia voluptas sit aspernatur aut odit aut fugit, sed quia consequuntur magni dolores eos qui ratione voluptatem sequi nesciunt. Neque porro quisquam est, qui dolorem ipsum quia dolor sit amet,</p>
  <a class="abs btn" style="left:112px;top:3700px;width:136px;height:44px">READ MORE
    <svg width="16" height="10" viewBox="0 0 16 10"><path d="M0 5h14M10 1l4 4-4 4" fill="none" stroke="#fff" stroke-width="1.6"/></svg></a>
  <div class="abs video" role="img" aria-label="Music video still of a bearded man at night with blurred city lights"></div>
  <div class="abs play" style="left:846px;top:3537px"><svg width="18" height="20" viewBox="0 0 18 20"><path d="M3 1l14 9-14 9z" fill="#222"/></svg></div>
</section>

<section class="contact">
  <div class="abs contact-bg"></div>
  <div class="abs contact-scene" role="img" aria-label="Smoky battlefield scene with a crouching figure on railway tracks"></div>
  <svg class="abs" style="left:0;top:3820px" width="1200" height="60" viewBox="0 0 1200 60">
    <path d="M0 38 Q600 -10 1200 38" fill="none" stroke="var(--red)" stroke-width="4"/>
  </svg>
  <h2 class="abs">GET IN TOUCH</h2>
  <div class="abs field" style="left:630px;top:4023px;width:215px;height:45px">First Name</div>
  <div class="abs field" style="left:870px;top:4023px;width:215px;height:45px">Last Name</div>
  <div class="abs field" style="left:630px;top:4083px;width:215px;height:45px">Mobile Number</div>
  <div class="abs field" style="left:870px;top:4083px;width:215px;height:45px">Email</div>
  <div class="abs field" style="left:630px;top:4142px;width:455px;height:114px">Message</div>
  <a class="abs btn submit">SUBMIT</a>
</section>

<footer class="abs">© copyrights 2019 All Rights Reserved</footer>

</body>
</html>
```